Calvera fine stockings - sexy cardboard box design needed!

We need a packaging design for a new online company based in Sydney called 'Calvera Hosiery'. We will be selling sexy stockings to our customers by Italian designers. We mainly feature lace stockings, an example of which, can be seen here:
http://www.brontevassipelli.example/italy-FASHION-WINTER

The design should be a cardboard pull out box, black in colour with the logo on the cover. We are looking for the logo to communicate sophistication and sexiness.

Examples of cardboard box shapes we would like are:
http://www.tradoquel.example/product-gs/583016274/High_quality_drawer_paper_box.html

http://www.tradoquel.example/product-gs/639152487/Cardboard_drawer_box.html

29 December:
I submitted a note when I extended the deadline, but cannot see it, so will write here for clarification. It has been difficult to choose the best design as the designs submitted were of such high quality. I want to have some people judge the designs, but because of the Christmas Season I have extended the deadline so that this can be done. Thanks.

Target Market(s)

The working professional woman.

Industry/Entity Type

Fashion

Requirements
Must have
• The words "Calvera Hosiery" on the cover of the box.

The box should be a sliding drawer.

The box size should be: (22*15*2.5cm).

Washing instructions and recycling logos on the back of the box. See example of uploaded file.

Nice to have
• It would be nice to have the background of the box a dark colour, maybe charcoal? But we are open to all ideas.
Should not have
• A stock photo on cover of box.

```html
<!DOCTYPE html>
<html lang="en">
<head>
<meta charset="utf-8">
<title>Calvera Hosiery – Box Cover</title>
<link rel="stylesheet" href="https://fonts.googleapis.com/css2?family=Marcellus&display=swap">
<style>
  :root {
    --charcoal: #3b3638;
    --lace-band: #332e30;
    --lace-band-edge: #2d292b;
    --rosette-dark: #262224;
    --rosette-light: #5c585a;
    --seal-black: #0c0a0b;
    --seal-ring: #8a8688;
    --name-white: #f4f2f3;
  }
  * { margin: 0; padding: 0; box-sizing: border-box; }
  html, body {
    width: 818px;
    height: 1200px;
    overflow: hidden;
    background: var(--charcoal);
  }
  .box-cover {
    position: relative;
    width: 818px;
    height: 1200px;
    background: var(--charcoal);
    overflow: hidden;
  }
  .lace-band {
    position: absolute;
    top: 0;
    left: 322px;
    width: 174px;
    height: 1200px;
    background: linear-gradient(90deg, var(--lace-band-edge) 0%, var(--lace-band) 20%, var(--lace-band) 80%, var(--lace-band-edge) 100%);
  }
  .seal {
    position: absolute;
    left: 215px;
    top: 333px;
    width: 388px;
    height: 388px;
  }
  .seal svg { display: block; width: 100%; height: 100%; }
  .brand-name {
    position: absolute;
    left: 0;
    top: 0;
    width: 388px;
    height: 388px;
    display: flex;
    align-items: center;
    justify-content: center;
    font-family: "Marcellus", serif;
    font-size: 66px;
    font-weight: 400;
    color: var(--name-white);
    letter-spacing: 1px;
    padding-bottom: 4px;
  }
</style>
</head>
<body>
  <main class="box-cover">
    <div class="lace-band" role="img" aria-label="Vertical band of black lace running down the centre of the cover"></div>

    <div class="seal">
      <svg viewBox="0 0 388 388" xmlns="http://www.w3.org/2000/svg">
        <defs>
          <radialGradient id="rosette-tone" cx="50%" cy="50%" r="50%">
            <stop offset="62%" stop-color="var(--rosette-light)"/>
            <stop offset="80%" stop-color="#46424480"/>
            <stop offset="100%" stop-color="var(--rosette-dark)"/>
          </radialGradient>
        </defs>
        <circle class="lace-rosette" cx="194" cy="194" r="192" fill="url(#rosette-tone)" role="img" aria-label="Circular lace rosette ornament framing the brand seal"/>
        <circle class="seal-disc" cx="194" cy="194" r="124" fill="var(--seal-black)"/>
        <circle class="seal-ring" cx="194" cy="194" r="114" fill="none" stroke="var(--seal-ring)" stroke-width="1.5" stroke-dasharray="1.5 2"/>
      </svg>
      <div class="brand-name">Calvera</div>
    </div>
  </main>
</body>
</html>
```